Recruitment of Archipel Workforce for the UK market

I want a website for the UK market to attract businesses and companies to come to us for Philipine labour. We want an information site that gives all information on what we do and how we can recruit Philippine labour.
This is a recruitment site for companies to contact us with their requirements for skilled workers coming from the Philipines over to the UK to work.

Target Market(s)

Uk Companies and businesses who want Philipine skilled workers

Industry/Entity Type

REcruitment

Coding

Number of Pages Required

5+ page

Font styles to use
Sans Serif

Colors
0054AA
0677BA
7BADD7
CADEEF
E8F1F8
0094D4
00A9DD
6FCCEA
C7EBF8
E9F6FB
EE7325
F08F49
F5BC92
FAE3D3
FDF4ED
EB3D1F
EC4F4E
F09395
F8D3D4
FCEDEE

Requirements
Must have
• Look professional and corperate with drop down menus for Home ,about, services,articles. training , contact us
Nice to have
• Look at Velmora recruitment- https://velmorarecruitment.example.co.uk/. This is my current site - https://www.trellanstaffing.example.com/
Should not have
• Cartoons or silly pictures , needs to be corperate looking

```html
<!DOCTYPE html>
<html lang="en">
<head>
<meta charset="utf-8">
<title>Archipel Workforce – Recruiting skilled workers for UK companies</title>
<link rel="stylesheet" href="https://fonts.googleapis.com/css2?family=Poppins:wght@400;600;700&family=Inter:wght@400;500&display=swap">
<style>
:root{
  --brand:#8b2f2f;
  --brand-dark:#7a2828;
  --ink:#111111;
  --text:#333333;
  --muted:#555555;
  --hero-bg:#efefef;
  --footer-bg:#f6f4f5;
  --white:#ffffff;
  --line:#9a9a9a;
}
*{box-sizing:border-box;margin:0;padding:0}
html,body{width:1200px;height:3705px;overflow:hidden}
body{position:relative;background:var(--white);font-family:"Inter",sans-serif;color:var(--text)}
.abs{position:absolute}
h1,h2,h3,.display{font-family:"Poppins",sans-serif;color:var(--ink)}

/* header */
.site-header{position:absolute;left:0;top:0;width:1200px;height:86px;background:var(--white);box-shadow:0 2px 6px rgba(0,0,0,.08);z-index:2}
.brand{position:absolute;left:112px;top:26px;font-family:"Poppins",sans-serif;font-weight:700;font-size:28px;color:var(--brand);letter-spacing:.5px}
.main-nav a{position:absolute;top:30px;transform:translateX(-50%);font-family:"Poppins",sans-serif;font-size:15px;color:#222;text-decoration:none}
.main-nav a.active{color:var(--brand);font-weight:600;font-size:18px;top:27px;border-bottom:2px solid var(--brand);padding-bottom:2px}

/* hero */
.hero{position:absolute;left:0;top:86px;width:1200px;height:598px;background:linear-gradient(135deg,#f3f3f3,#e9e9e9 60%,#f1f1f1)}
.hero-title{left:102px;top:80px;font-size:68px;line-height:76px;font-weight:700;width:480px}
.btn{display:block;background:var(--brand);color:var(--white);font-family:"Poppins",sans-serif;font-weight:600;text-align:center;text-decoration:none;border-radius:2px}
.hero-btn{left:102px;top:343px;width:154px;height:50px;line-height:50px;font-size:19px}
.hero-lead{left:616px;top:84px;font-family:"Poppins",sans-serif;font-size:37px;line-height:47px;color:#111;width:480px}
.hero-copy{left:616px;top:232px;width:470px;font-size:15px;line-height:31px;color:#333}
.stat{font-family:"Poppins",sans-serif;color:#111}
.stat b{font-size:40px;font-weight:700;vertical-align:middle}
.stat span{display:inline-block;font-size:16px;line-height:21px;vertical-align:middle;margin-left:14px;color:#333}

/* working together */
.section-title{width:1200px;left:0;text-align:center;font-weight:600}
.cards .card{position:absolute;top:826px;width:240px;height:239px;background:var(--brand)}
.card svg{position:absolute;left:82px;top:55px}
.card h3{position:absolute;left:0;width:240px;top:154px;text-align:center;color:var(--white);font-size:27px;font-weight:600}

/* media */
.media-band{left:0;top:1151px;width:1200px;height:535px;background:linear-gradient(110deg,#6b7a8c 0%,#8a93a0 30%,#4f5f70 55%,#6a5c4c 80%,#3f4650 100%)}
.play{left:562px;top:1379px}

/* about */
.about-title{left:100px;top:1778px;font-size:46px;line-height:68px;font-weight:700;width:380px}
.read-more{left:102px;top:2082px;font-family:"Poppins",sans-serif;font-weight:600;font-size:18px;color:#111;text-decoration:none}
.photo{position:absolute}
.caption{position:absolute;text-align:center;font-family:"Poppins",sans-serif;font-weight:600;font-size:21px;color:#111}

/* contact form */
.field{position:absolute;border:1px solid var(--line);background:var(--white);font-size:15px;color:#444;padding:0 19px;display:flex;align-items:center}
.field.area{align-items:flex-start;padding-top:15px}
.send-btn{left:518px;top:3071px;width:163px;height:52px;line-height:52px;font-size:18px}

/* footer */
.site-footer{left:0;top:3202px;width:1200px;height:503px;background:var(--footer-bg)}
.footer-brand{left:102px;top:3288px;font-family:"Poppins",sans-serif;font-weight:700;font-size:34px;color:var(--brand)}
.social{position:absolute;top:3373px;width:38px;height:38px;border-radius:50%;background:var(--brand)}
.small{font-size:15px;line-height:31px;color:#333}
.footer-h{left:449px;top:3284px;font-size:22px;font-weight:600}
.contact-line{position:absolute;left:478px;font-size:15px;color:#333}
.contact-icon{position:absolute;left:449px}
.footer-note{left:732px;top:3280px;width:370px;font-family:"Poppins",sans-serif;font-weight:600;font-size:21px;line-height:31px;color:#111}
.map{left:732px;top:3443px;width:363px;height:177px;background:linear-gradient(135deg,#7f9df0,#6f8fe8)}
</style>
</head>
<body>

<header class="site-header">
  <div class="brand">Archipel Workforce</div>
  <nav class="main-nav">
    <a href="#" class="active" style="left:543px">Home</a>
    <a href="#" style="left:635px">About</a>
    <a href="#" style="left:731px">Services</a>
    <a href="#" style="left:835px">Articles</a>
    <a href="#" style="left:935px">Training</a>
    <a href="#" style="left:1050px">Contact us</a>
  </nav>
</header>

<section class="hero">
  <h1 class="abs hero-title">Welcome To Archipel Workforce</h1>
  <a href="#" class="abs btn hero-btn">Get Started</a>
  <p class="abs hero-lead">Recruiting and placing skilled Philippine workers into UK companies</p>
  <p class="abs hero-copy">We source skilled workers directly from the Philippines to work in the UK. With offices , training locations and specialist recruiters we can find the highest quality individuals to add value and resources to any UK buisness.</p>
  <div class="abs stat" style="left:618px;top:396px"><b>4000+</b><span>People<br>Recruited</span></div>
  <div class="abs stat" style="left:882px;top:396px"><b>200+</b><span>Happy<br>Clients</span></div>
  <div class="abs stat" style="left:618px;top:490px"><b>20+</b><span>Countries</span></div>
</section>

<h2 class="abs section-title" style="top:748px;font-size:32px">Working Together</h2>
<div class="cards">
  <div class="card" style="left:104px">
    <svg width="76" height="76" viewBox="0 0 76 76" fill="none" stroke="#fff" stroke-width="3"><circle cx="20" cy="16" r="8"/><circle cx="38" cy="12" r="8"/><circle cx="56" cy="16" r="8"/><circle cx="38" cy="52" r="18"/><path d="M32 46a6 6 0 1 1 8 5v4M38 60v1"/></svg>
    <h3>What we do</h3>
  </div>
  <div class="card" style="left:354px">
    <svg width="76" height="76" viewBox="0 0 76 76" fill="none" stroke="#fff" stroke-width="3"><circle cx="38" cy="18" r="8"/><path d="M26 40c0-7 6-12 12-12s12 5 12 12"/><path d="M6 30v20l16 18M70 30v20L54 68M14 44l10 10M62 44L52 54"/></svg>
    <h3>How we help</h3>
  </div>
  <div class="card" style="left:605px">
    <svg width="76" height="76" viewBox="0 0 76 76" fill="none" stroke="#fff" stroke-width="3"><path d="M66 10C46 10 32 22 24 40l12 12c18-8 30-22 30-42z"/><circle cx="48" cy="28" r="6"/><path d="M24 40H12l10-12h12M36 52v12l12-10V42M20 56l-10 10"/></svg>
    <h3>Where to start</h3>
  </div>
  <div class="card" style="left:856px">
    <svg width="76" height="76" viewBox="0 0 76 76" fill="none" stroke="#fff" stroke-width="3"><circle cx="38" cy="38" r="14"/><path d="M24 38h28M38 24c-6 8-6 20 0 28M38 24c6 8 6 20 0 28"/><rect x="6" y="6" width="18" height="14"/><path d="M6 6l9 8 9-8"/><rect x="54" y="6" width="14" height="20"/><path d="M10 52c0 10 8 18 18 18M60 60h8v10h-8z"/></svg>
    <h3>Contact us</h3>
  </div>
</div>

<div class="abs media-band" role="img" aria-label="Video still: engineer in hard hat working with digital industrial interface screens"></div>
<svg class="abs play" width="76" height="76" viewBox="0 0 76 76"><circle cx="38" cy="38" r="36" fill="#fff" fill-opacity=".55"/><circle cx="38" cy="38" r="29" fill="var(--brand)"/><path d="M31 27l19 11-19 11z" fill="#fff"/></svg>

<h2 class="abs about-title">What the business is about Archipel Workforce</h2>
<a href="#" class="abs read-more">Read More
  <svg width="16" height="14" viewBox="0 0 16 14" style="margin-left:6px"><path d="M1 7h12M8 2l5 5-5 5" stroke="#111" stroke-width="2.6" fill="none"/></svg></a>

<div class="photo" style="left:479px;top:1770px;width:301px;height:383px;background:linear-gradient(160deg,#6f6250,#8a6b4e 50%,#5a4b40)" role="img" aria-label="Photo of welders inspecting a pipe"></div>
<div class="caption" style="left:479px;top:2170px;width:290px">Welders</div>
<div class="photo" style="left:796px;top:1770px;width:299px;height:383px;background:linear-gradient(160deg,#b7a89a,#d8cfc8 50%,#8a7f78)" role="img" aria-label="Photo of a smiling engineering team"></div>
<div class="caption" style="left:796px;top:2170px;width:280px">Engineer</div>

<div class="photo" style="left:104px;top:2288px;width:318px;height:325px;background:linear-gradient(160deg,#d9c8a8,#a68a62 55%,#5e4c38)" role="img" aria-label="Photo of a construction worker using a tablet"></div>
<div class="caption" style="left:104px;top:2637px;width:318px">UK Skilled Workers List</div>
<div class="photo" style="left:440px;top:2288px;width:318px;height:325px;background:linear-gradient(160deg,#22303a,#3c5260 55%,#1d262d)" role="img" aria-label="Photo of a hand touching a digital network display"></div>
<div class="caption" style="left:440px;top:2637px;width:318px">Sponsor Licence</div>
<div class="photo" style="left:777px;top:2288px;width:317px;height:325px;background:linear-gradient(160deg,#4a4a52,#cfcbd0 55%,#8e8a90)" role="img" aria-label="Photo of a person reviewing documents"></div>
<div class="caption" style="left:777px;top:2637px;width:317px">Recruitment Timeline</div>

<h2 class="abs section-title" style="top:2736px;font-size:34px">Contact us today</h2>
<form>
  <div class="field" style="left:119px;top:2807px;width:474px;height:54px">Enter Name</div>
  <div class="field" style="left:607px;top:2807px;width:474px;height:54px">Enter Phone</div>
  <div class="field" style="left:119px;top:2879px;width:474px;height:54px">Enter Email</div>
  <div class="field" style="left:607px;top:2879px;width:474px;height:54px">Enter Address</div>
  <div class="field area" style="left:119px;top:2947px;width:962px;height:91px">Message</div>
  <a href="#" class="abs btn send-btn">Send Message</a>
</form>

<footer class="abs site-footer"></footer>
<div class="abs footer-brand">Archipel Workforce</div>
<div class="social" style="left:105px" aria-label="Social link"></div>
<div class="social" style="left:156px" aria-label="Social link"></div>
<div class="social" style="left:207px" aria-label="Social link"></div>
<div class="social" style="left:259px" aria-label="Social link"></div>
<p class="abs small" style="left:102px;top:3440px">Copyrights@2023.Archipel Workforce.<br>All Rights Reserved</p>

<h3 class="abs footer-h">Contact Us</h3>
<svg class="contact-icon" style="top:3335px" width="16" height="16" viewBox="0 0 16 16"><path d="M3 1l3 3-2 2c1 2 3 4 6 6l2-2 3 3-2 2C7 15 1 9 1 3z" fill="#222"/></svg>
<div class="contact-line" style="top:3332px">07700 900481</div>
<svg class="contact-icon" style="top:3375px" width="16" height="16" viewBox="0 0 16 16"><path d="M3 1l3 3-2 2c1 2 3 4 6 6l2-2 3 3-2 2C7 15 1 9 1 3z" fill="#222"/></svg>
<div class="contact-line" style="top:3372px">sales@archipelworkforce.example.com</div>
<svg class="contact-icon" style="top:3416px" width="14" height="18" viewBox="0 0 14 18"><path d="M7 1a6 6 0 0 1 6 6c0 4-6 10-6 10S1 11 1 7a6 6 0 0 1 6-6z" fill="#222"/><circle cx="7" cy="7" r="2.2" fill="#fff"/></svg>
<p class="abs small" style="left:478px;top:3409px">Linden Court,<br>Eastbridge EB4 2<br>United Kingdom</p>

<p class="abs footer-note">We recruit the finest talent available with our dedicated 200 strong team. Our centres are highlighted in red dots on the map.</p>
<div class="abs map" role="img" aria-label="Map of the Philippines with recruitment centres marked by red dots"></div>

</body>
</html>
```